Website redesign www.marigoldlawpc.com law firm site

Need to redesign the website that I currently have to look more modern and professional. Would also like to be able to make updates and post without having a huge hassle. See current www.marigoldlawpc.com. I just think that it looks very immature and it's very templated there's no ability for me to make posts or Add links or anything like that

Target Market(s)

California people looking for a powerhouse attorney in

Industry/Entity Type

Legal

Number of Pages Required

3 page

Font styles to use
Serif
Sans Serif

Colors
ec1f27
000000
ffffff

Requirements
Must have
• Must be mobile friendly. Must look professional and have ability to post links to other websites. Must have ability to post blogs or articles. Would like to be able to read my FeeTrove account and also have the ability to upload forms for people to download
Nice to have
• Simple design easy to use and not cluttered with too much text

```html
<!DOCTYPE html>
<html lang="en">
<head>
<meta charset="utf-8">
<title>Marigold Law P.C.</title>
<link rel="stylesheet" href="https://fonts.googleapis.com/css2?family=Roboto+Slab:wght@400;700&family=Open+Sans:wght@400;600;700&display=swap">
<style>
:root{
  --red:#ec1f27;
  --red-dark:#b3121a;
  --black:#000;
  --ink:#222;
  --grey:#555;
  --white:#fff;
  --footer:#2b2b2b;
  --footer-bottom:#161616;
  --line:#ddd;
}
*{box-sizing:border-box;margin:0;padding:0}
html,body{width:1200px;height:3644px;overflow:hidden}
body{position:relative;background:var(--white);font-family:"Open Sans",sans-serif;color:var(--ink)}
.abs{position:absolute}
.serif{font-family:"Roboto Slab",serif}
.accent{color:var(--red)}

/* header */
.site-header{position:absolute;left:0;top:0;width:1200px;height:120px}
.brand{position:absolute;left:100px;top:26px;font-family:"Roboto Slab",serif;font-size:40px;color:var(--red);letter-spacing:1px}
.brand-rule{position:absolute;left:100px;top:90px;width:300px;height:2px;background:var(--red)}
.contact-chip{position:absolute;top:38px;display:flex;align-items:center;gap:12px;font-size:17px;color:var(--ink)}
.chip-icon{width:36px;height:36px;border-radius:50%;background:var(--red);display:flex;align-items:center;justify-content:center}

.main-nav{position:absolute;left:0;top:120px;width:1200px;height:58px;background:var(--red)}
.main-nav a{position:absolute;top:0;height:58px;line-height:58px;color:var(--white);font-weight:700;font-size:16px;text-decoration:none}
.main-nav a.active{background:var(--footer-bottom);padding:0 34px}

/* hero */
.hero{position:absolute;left:0;top:178px;width:1200px;height:472px;background:linear-gradient(90deg,#2a160d 0%,#4a2715 45%,#7a4423 75%,#3a1d0f 100%)}
.hero-title{position:absolute;left:100px;top:158px;width:560px;font-family:"Roboto Slab",serif;font-size:28px;line-height:42px;color:var(--white)}
.dots{position:absolute;display:flex;gap:10px}
.dots span{width:13px;height:13px;border-radius:50%;background:var(--white)}
.dots span.on{background:var(--red);border:2px solid var(--white)}

/* section titles */
.section-title{position:absolute;left:0;width:1200px;text-align:center;font-family:"Roboto Slab",serif;font-size:34px;color:var(--ink)}
.title-rule{position:absolute;left:450px;width:300px;height:2px;background:var(--ink)}

/* welcome */
.intro{position:absolute;left:100px;top:780px;width:1000px;text-align:center;font-size:13.5px;line-height:22px;color:var(--grey)}
.btn-dark{position:absolute;left:532px;top:872px;width:136px;height:38px;background:#333;color:var(--white);font-family:"Roboto Slab",serif;font-size:16px;text-align:center;line-height:38px}
.pillar{position:absolute;top:955px;width:300px;text-align:center}
.pillar h3{font-family:"Roboto Slab",serif;font-weight:400;font-size:26px;color:var(--ink)}
.pillar .icon{width:86px;height:86px;border-radius:50%;background:var(--red);margin:22px auto 0;display:flex;align-items:center;justify-content:center}
.pillar p{margin:18px auto 0;width:270px;font-size:13.5px;line-height:20px;color:var(--grey)}

/* practice */
.practice{position:absolute;left:0;top:1230px;width:1200px;height:555px;background:linear-gradient(135deg,#c3131b 0%,#e01f27 40%,#a90f16 75%,#d11820 100%)}
.practice .section-title{color:var(--white);top:26px}
.area{position:absolute;width:240px;color:var(--white);font-size:13px;line-height:17px}
.area h4{font-family:"Roboto Slab",serif;font-size:17px;font-weight:700;margin-bottom:2px}
.area.left{text-align:right}
.area.center{text-align:center}

/* blog */
.post{position:absolute;top:1943px;width:473px}
.post-date{position:absolute;left:0;top:0;width:36px;height:44px;background:var(--red);color:var(--white);text-align:center;font-size:12px;line-height:14px;padding-top:6px;font-weight:700}
.post-head{position:absolute;left:50px;top:0;width:420px;font-family:"Roboto Slab",serif;font-size:17px;line-height:23px;color:var(--ink)}
.post-image{position:absolute;left:0;top:69px;width:473px;height:170px}
.post-text{position:absolute;left:0;top:255px;width:473px;font-size:13.5px;line-height:19px;color:var(--grey)}
.dots.grey span{width:9px;height:9px;background:#ccc}
.dots.grey span.on{background:var(--red);border:none}

/* testimonials */
.voices{position:absolute;left:0;top:2350px;width:1200px;height:390px;background:linear-gradient(135deg,#b70f17 0%,#e3222a 45%,#a50d14 100%)}
.voices .section-title{color:var(--white);top:34px}
.voice{position:absolute;top:112px;width:330px;text-align:center;color:var(--white)}
.avatar{width:116px;height:116px;border-radius:50%;margin:0 auto;background:linear-gradient(160deg,#c9ccd2,#7b8290);border:5px solid var(--white)}
.voice .quote{position:relative;margin-top:20px;padding-left:70px;text-align:left;font-style:italic;font-size:13.5px;line-height:18px}
.voice .mark{position:absolute;left:0;top:-14px;font-family:"Roboto Slab",serif;font-size:86px;line-height:86px;font-style:normal;color:rgba(255,255,255,.55)}
.voice .name{margin-top:18px;font-weight:700;font-size:15px}
.arrow{position:absolute;top:192px;width:34px;height:34px;border-radius:50%;background:#1a1a1a;display:flex;align-items:center;justify-content:center}

/* ratings */
.ratings-sub{position:absolute;left:0;top:2860px;width:1200px;text-align:center;font-size:14px;color:var(--ink)}
.badge-box{position:absolute;top:2932px;width:277px;height:114px;border:1px solid var(--line);display:flex;align-items:center;justify-content:center}

/* newsletter */
.newsletter{position:absolute;left:0;top:3135px;width:1200px;height:146px;background:var(--red)}
.newsletter h3{position:absolute;left:187px;top:36px;font-family:"Roboto Slab",serif;font-weight:400;font-size:26px;color:var(--white)}
.newsletter p{position:absolute;left:187px;top:76px;width:340px;font-size:12px;line-height:16px;color:var(--white)}
.nl-input{position:absolute;left:593px;top:45px;width:371px;height:44px;border:1px solid var(--white);color:var(--white);font-size:12px;line-height:42px;padding-left:16px}
.nl-btn{position:absolute;left:981px;top:45px;width:119px;height:44px;background:var(--black);color:var(--white);font-size:12px;font-weight:700;text-align:center;line-height:44px;letter-spacing:.5px}

/* footer */
.site-footer{position:absolute;left:0;top:3281px;width:1200px;height:319px;background:var(--footer);color:#ddd;font-size:13px}
.site-footer h5{position:absolute;top:42px;font-family:"Roboto Slab",serif;font-weight:400;font-size:20px;color:var(--white)}
.quick-links{position:absolute;left:100px;top:88px;list-style:none}
.quick-links li{height:30.5px;font-size:13px}
.quick-links li::before{content:"› ";color:var(--red)}
.quick-links li.active{color:var(--red)}
.contact-block{position:absolute;left:301px;top:86px;line-height:19px}
.contact-line{display:flex;align-items:center;gap:8px;margin-top:16px}
.map{position:absolute;left:554px;top:84px;width:255px;height:165px;background:linear-gradient(135deg,#eceae4,#dcd8ce)}
.pay-name{position:absolute;left:850px;top:142px;display:flex;align-items:center;gap:12px;font-family:"Open Sans",sans-serif;font-weight:600;font-size:30px;color:var(--white)}
.pay-name .mark{width:22px;height:22px;background:var(--red)}
.footer-bottom{position:absolute;left:0;top:3600px;width:1200px;height:44px;background:var(--footer-bottom);color:#ccc;font-size:13px}
.socials{position:absolute;right:100px;top:9px;display:flex;gap:10px}
.socials span{width:26px;height:26px;border-radius:50%;background:#3c6fb6}
</style>
</head>
<body>

<header class="site-header">
  <div class="brand">Marigold Law P.C.</div>
  <div class="brand-rule"></div>
  <div class="contact-chip" style="left:656px">
    <span class="chip-icon"><svg width="18" height="18" viewBox="0 0 24 24"><path fill="#fff" d="M6.6 10.8a15 15 0 0 0 6.6 6.6l2.2-2.2c.3-.3.7-.4 1-.2 1.1.4 2.3.6 3.6.6.6 0 1 .4 1 1V20c0 .6-.4 1-1 1A17 17 0 0 1 3 4c0-.6.4-1 1-1h3.5c.6 0 1 .4 1 1 0 1.3.2 2.5.6 3.6.1.3 0 .7-.2 1z"/></svg></span>
    (530) 555-0142
  </div>
  <div class="contact-chip" style="left:855px;font-size:15px">
    <span class="chip-icon"><svg width="18" height="14" viewBox="0 0 18 14"><rect x="1" y="1" width="16" height="12" fill="#fff"/><path d="M1 1l8 7 8-7" fill="none" stroke="#ec1f27" stroke-width="1.6"/></svg></span>
    dana@marigoldlawgroup.com
  </div>
</header>

<nav class="main-nav">
  <a class="active" style="left:100px">Home</a>
  <a style="left:258px">Attorney Profile</a>
  <a style="left:460px">Practice Areas &#9662;</a>
  <a style="left:668px">Client Reviews</a>
  <a style="left:862px">Links</a>
  <a style="left:984px">Contact Us</a>
</nav>

<section class="hero" role="img" aria-label="Wooden judge's gavel on a desk in front of law books">
  <h1 class="hero-title" style="font-weight:400">A Boutique Law Firm Opportunity For Clients Who Want To Enjoy All The Advantages Of Dana's Broad Legal Experience And Education.</h1>
  <div class="dots" style="left:104px;top:341px"><span class="on"></span><span></span><span></span><span></span></div>
</section>

<section class="welcome">
  <h2 class="section-title" style="top:700px;font-weight:400">Welcome to <span class="accent">Marigold Law P.C</span></h2>
  <div class="title-rule" style="top:756px"></div>
  <p class="intro">Marigold Law P.C. is owned by Dana L. Marigold, a dedicated and caring professional who uses her broad range of skills as a California lawyer to bring consumers and business owners exceptionally strong legal representation that achieves best results. She works with people from across the northern region of California, from the Northern border to the Central Valley region.</p>
  <div class="btn-dark">Read More</div>

  <div class="pillar" style="left:112px">
    <h3>Mission</h3>
    <div class="icon"><svg width="46" height="46" viewBox="0 0 46 46"><circle cx="21" cy="25" r="17" fill="none" stroke="#fff" stroke-width="4"/><circle cx="21" cy="25" r="9" fill="none" stroke="#fff" stroke-width="4"/><circle cx="21" cy="25" r="3" fill="#fff"/><path d="M21 25L40 6" stroke="#fff" stroke-width="3"/><path d="M36 4l6 0-2 6z" fill="#fff"/></svg></div>
    <p>Sed ut perspiciatis unde omnis iste natus error sit voluptatem accusantium doloremque laudantium,</p>
  </div>
  <div class="pillar" style="left:450px">
    <h3>Vision</h3>
    <div class="icon"><svg width="50" height="30" viewBox="0 0 50 30"><path d="M2 15C10 3 40 3 48 15 40 27 10 27 2 15z" fill="#fff"/><circle cx="25" cy="15" r="8" fill="#ec1f27"/><circle cx="25" cy="15" r="3.5" fill="#fff"/></svg></div>
    <p>Sed ut perspiciatis unde omnis iste natus error sit voluptatem accusantium doloremque laudantium,</p>
  </div>
  <div class="pillar" style="left:788px">
    <h3>Values</h3>
    <div class="icon"><svg width="44" height="40" viewBox="0 0 44 40"><rect x="4" y="24" width="7" height="14" fill="#fff"/><rect x="15" y="18" width="7" height="20" fill="#fff"/><rect x="26" y="12" width="7" height="26" fill="#fff"/><path d="M4 18L16 10l8 4L38 3" fill="none" stroke="#fff" stroke-width="3"/><path d="M34 1h7v7z" fill="#fff"/></svg></div>
    <p>Sed ut perspiciatis unde omnis iste natus error sit voluptatem accusantium doloremque laudantium,</p>
  </div>
</section>

<section class="practice" role="img" aria-label="Red faceted triangle pattern background">
  <h2 class="section-title" style="font-weight:400">Practice Areas</h2>
  <div class="abs" style="left:345px;top:88px;width:510px;height:1px;background:rgba(255,255,255,.35)"></div>
  <svg class="abs" style="left:0;top:0" width="1200" height="555" viewBox="0 0 1200 555">
    <path d="M318 555A282 282 0 0 1 882 555" fill="none" stroke="#fff" stroke-width="5"/>
    <g fill="#fff">
      <circle cx="600" cy="273" r="30"/>
      <circle cx="432" cy="252" r="30"/>
      <circle cx="768" cy="247" r="30"/>
      <circle cx="357" cy="354" r="30"/>
      <circle cx="838" cy="347" r="30"/>
      <circle cx="323" cy="470" r="30"/>
      <circle cx="880" cy="466" r="30"/>
    </g>
    <g fill="#ec1f27">
      <circle cx="592" cy="264" r="6"/><circle cx="608" cy="264" r="6"/><rect x="584" y="272" width="32" height="13" rx="5"/>
      <circle cx="432" cy="252" r="15"/>
      <path d="M341 356l16-15 16 15h-5v13h-22v-13z"/>
      <rect x="307" y="462" width="32" height="22" rx="3"/>
      <path d="M866 470l10-10 4 4-10 10zM876 470l6 6 12 0 0 4-18 0z"/>
      <path d="M822 355a16 14 0 0 1 32 0h4v4h-40v-4z"/>
    </g>
    <circle cx="760" cy="247" r="8" fill="none" stroke="#ec1f27" stroke-width="4"/>
    <circle cx="776" cy="247" r="8" fill="none" stroke="#ec1f27" stroke-width="4"/>
    <text x="432" y="258" text-anchor="middle" font-family="Open Sans,sans-serif" font-size="17" font-weight="700" fill="#fff">$</text>
    <rect x="310" y="468" width="26" height="2" fill="#fff"/>
    <rect x="460" y="451" width="282" height="2" fill="#fff"/>
  </svg>
  <div class="abs serif" style="left:380px;top:396px;width:440px;text-align:center;font-size:40px;color:#fff">Marigold Law P.C.</div>

  <div class="area center" style="left:480px;top:182px"><h4>Family Law</h4>Sed ut perspiciatis unde omnis<br>sit voluptatem accusantium</div>
  <div class="area left" style="left:158px;top:198px"><h4>Bankruptcy</h4>Sed ut perspiciatis unde omnis<br>sit voluptatem accusantium</div>
  <div class="area" style="left:808px;top:198px"><h4>Criminal Law</h4>Sed ut perspiciatis unde omnis<br>sit voluptatem accusantium</div>
  <div class="area left" style="left:70px;top:303px"><h4>Real Estate Law</h4>Sed ut perspiciatis unde omnis<br>sit voluptatem accusantium</div>
  <div class="area" style="left:884px;top:303px"><h4>Civil Litigation</h4>Sed ut perspiciatis unde omnis<br>sit voluptatem accusantium</div>
  <div class="area left" style="left:40px;top:428px"><h4>Business Law</h4>Sed ut perspiciatis unde omnis<br>sit voluptatem accusantium</div>
  <div class="area" style="left:926px;top:428px"><h4>Unlawful Detainer</h4>Sed ut perspiciatis unde omnis<br>sit voluptatem accusantium</div>
</section>

<section class="blog">
  <h2 class="section-title" style="top:1834px;font-weight:400">Latest From <span class="accent">Our Blog</span></h2>
  <div class="title-rule" style="top:1892px"></div>
  <article class="post" style="left:100px">
    <div class="post-date">17<sup>th</sup><br>Feb</div>
    <h3 class="post-head" style="font-weight:400">Lorem ipsum dolor sit amet, consectetuer adipiscing elit doloremque.</h3>
    <div class="post-image" role="img" aria-label="Gavel resting on a historic constitution document" style="background:linear-gradient(120deg,#d8b47a,#9b6a34 55%,#4a2a14)"></div>
    <p class="post-text">Fusce elementum, nulla vel pellentes consequat, ante nulla hendrerit arcu, ac tincidunt mauris lacus sed leo. vamus suscipit molestie vestibulum. Lorem ipsum dolor sit amet,</p>
  </article>
  <article class="post" style="left:627px">
    <div class="post-date">17<sup>th</sup><br>Feb</div>
    <h3 class="post-head" style="font-weight:400">Lorem ipsum dolor sit amet, consectetuer adipiscing elit doloremque.</h3>
    <div class="post-image" role="img" aria-label="Scales of justice in front of a courtroom" style="background:linear-gradient(120deg,#5a2a1a,#9c5a34 50%,#3a1c10)"></div>
    <p class="post-text">Fusce elementum, nulla vel pellentes consequat, ante nulla hendrerit arcu, ac tincidunt mauris lacus sed leo. vamus suscipit molestie vestibulum. Lorem ipsum dolor sit amet,</p>
  </article>
  <div class="dots grey" style="left:571px;top:2282px"><span class="on"></span><span></span><span></span><span></span></div>
</section>

<section class="voices" role="img" aria-label="Red faceted triangle pattern background">
  <h2 class="section-title" style="font-weight:400">What Peoples Say</h2>
  <div class="arrow" style="left:61px"><svg width="12" height="12" viewBox="0 0 12 12"><path d="M8 1L3 6l5 5" fill="none" stroke="#fff" stroke-width="2"/></svg></div>
  <div class="arrow" style="left:1105px"><svg width="12" height="12" viewBox="0 0 12 12"><path d="M4 1l5 5-5 5" fill="none" stroke="#fff" stroke-width="2"/></svg></div>
  <div class="voice" style="left:100px">
    <div class="avatar" role="img" aria-label="Client portrait"></div>
    <p class="quote"><span class="mark">&ldquo;</span>Lorem ipsum dolor sit amet, consectetuer adipiscing elit, sed diam nonummy Lorem ipsum dolor sit amet, consectetuer adipiscing elit.</p>
    <p class="name">- Consectetue Radipiscing</p>
  </div>
  <div class="voice" style="left:435px">
    <div class="avatar" role="img" aria-label="Client portrait"></div>
    <p class="quote"><span class="mark">&ldquo;</span>Lorem ipsum dolor sit amet, consectetuer adipiscing elit, sed diam nonummy Lorem ipsum dolor sit amet, consectetuer adipiscing elit.</p>
    <p class="name">- Diam Nonummy</p>
  </div>
  <div class="voice" style="left:770px">
    <div class="avatar" role="img" aria-label="Client portrait"></div>
    <p class="quote"><span class="mark">&ldquo;</span>Lorem ipsum dolor sit amet, consectetuer adipiscing elit, sed diam nonummy Lorem ipsum dolor sit amet, consectetuer adipiscing elit.</p>
    <p class="name">- Dolor Sitamet</p>
  </div>
</section>

<section class="ratings">
  <h2 class="section-title" style="top:2780px;font-weight:400">Ratings and <span class="accent">Reviews</span></h2>
  <div class="title-rule" style="top:2836px;background:#999;height:1px"></div>
  <p class="ratings-sub">Lawyer Dana L. Marigold, Esq. &nbsp;&nbsp;|&nbsp;&nbsp; Featured Attorney Bankruptcy / Chapter 7</p>
  <div class="badge-box" style="left:136px"><svg width="90" height="80"><rect x="5" y="5" width="80" height="70" rx="6" fill="none" stroke="#1d3f7a" stroke-width="3"/></svg></div>
  <div class="badge-box" style="left:462px"><svg width="90" height="90"><circle cx="45" cy="45" r="40" fill="none" stroke="#444" stroke-width="3"/></svg></div>
  <div class="badge-box" style="left:787px"><svg width="220" height="30"><rect x="5" y="5" width="210" height="20" fill="#1d3f7a"/></svg></div>
</section>

<section class="newsletter">
  <svg class="abs" style="left:100px;top:44px" width="62" height="50" viewBox="0 0 62 50"><rect x="2" y="2" width="58" height="46" fill="none" stroke="#fff" stroke-width="3"/><path d="M2 2l29 24L60 2M2 48l22-20M60 48L38 28" fill="none" stroke="#fff" stroke-width="3"/></svg>
  <h3>Subscribe To Our Newsletter</h3>
  <p>Sign up today for short legal news, practical tips and firm updates sent to you.</p>
  <div class="nl-input">Enter Your Email Here</div>
  <div class="nl-btn">SUBSCRIBE</div>
</section>

<footer class="site-footer">
  <h5 style="left:100px">Quick <span class="accent">Links</span></h5>
  <ul class="quick-links">
    <li class="active">Home</li><li>Attorney Profile</li><li>Practice Areas</li><li>Client Reviews</li><li>Links</li><li>Blog</li><li>Contact Us</li>
  </ul>
  <h5 style="left:301px">Contact <span class="accent">Details</span></h5>
  <div class="contact-block">
    <p>Marigold Law P.C<br>410 Orchard Avenue<br>Suite 200, Redding, CA 96001</p>
    <div class="contact-line"><svg width="14" height="14" viewBox="0 0 24 24"><path fill="#ddd" d="M6.6 10.8a15 15 0 0 0 6.6 6.6l2.2-2.2c.3-.3.7-.4 1-.2 1.1.4 2.3.6 3.6.6.6 0 1 .4 1 1V20c0 .6-.4 1-1 1A17 17 0 0 1 3 4c0-.6.4-1 1-1h3.5c.6 0 1 .4 1 1 0 1.3.2 2.5.6 3.6.1.3 0 .7-.2 1z"/></svg>(530) 555-0142</div>
    <div class="contact-line"><svg width="14" height="14" viewBox="0 0 14 14"><rect x="1" y="3" width="12" height="9" fill="none" stroke="#ddd" stroke-width="1.5"/><rect x="4" y="1" width="6" height="4" fill="#ddd"/></svg>(888) 555-0193</div>
    <div class="contact-line"><svg width="14" height="12" viewBox="0 0 14 12"><rect x="1" y="1" width="12" height="10" fill="#ddd"/><path d="M1 1l6 5 6-5" fill="none" stroke="#2b2b2b" stroke-width="1.2"/></svg>dana@marigoldlawgroup.com</div>
  </div>
  <h5 style="left:554px">Location <span class="accent">Map</span></h5>
  <div class="map" role="img" aria-label="Street map showing the office location"></div>
  <svg class="abs" style="left:668px;top:138px" width="22" height="30" viewBox="0 0 22 30"><path d="M11 29C4 18 1 14 1 10a10 10 0 0 1 20 0c0 4-3 8-10 19z" fill="#ec1f27"/><circle cx="11" cy="10" r="4" fill="#fff"/></svg>
  <div class="pay-name"><span class="mark"></span>FeeTrove</div>
</footer>

<div class="footer-bottom">
  <p class="abs" style="left:100px;top:13px">&copy; 2016 Marigold Law P.C. All Rights Reserved.</p>
  <div class="socials"><span></span><span></span><span></span></div>
</div>

</body>
</html>
```